Web design for small empirical brand consulting company that will sell a web-based brand tool

We need a totally new and very appealing website:
Purpose: We want to attract lots of potential customers with this website... especially, we want to sell our web-based tool valuquant®... we want to be perceived as innovative, trendy, but solid and reliable… we want customers go to the website, login at „valuquant®“ (see structure), and perceive how it works.. and the contacting us or in the near future being able to buy a login and work with the tool… so we want to a) inform (on the website or send the url to customers) and b) to „force“ potential customers getting in contact with us…
Structure (e.g.): Must Home, valuquant®, About us, Contact (incl. legal notice); we are open for more, Nice to have e.g. references/clients, press... for example, we publish a nice book in a couple of months and might want to show it somewhere on the website as well...)
Layout: We would like to have more/mainly figures - may be animated or something like that – in specific those on slides 7 and 8 as well as 6 and 9 (which would be for our web-based tool valuquant®...)... excellent, but simple and with few text…
Fonts: Eurostile; CMYK 100/23/100/19, CMYK 0/0/0/70
Logo: Would you please use the lorentavo-logo used in this file?
Social Media: we think that it might make sense to be connected to chatterbay, quipline and so on as well…
Phantasy: May be it is possible to have something between a classic marketing research and an e-commerce website... just a thought... because it is mainly about the new tool that will be assessable through a login... but customers might want to contact us or vice versa in order to check how the tool will work (btw: you do not have further info about valuquant® here... I know)… I dream of having a site where people go to and by components of our tool like at brimbo… click and buy and go for it…
It is possible to program it in php or java? Thanks.
Pages I personally like: Don’t know if that helps, but I personally like those websites just they seem so simple: http:// www.pellivarn.com/, http://www.craftelune.net/... but I am veeery open
Pages I do not like anymore: my own www.lorentavo.ch

```html
<!DOCTYPE html>
<html lang="en">
<head>
<meta charset="utf-8">
<title>lorentavo – Brand research and brand consulting</title>
<link rel="stylesheet" href="https://fonts.googleapis.com/css2?family=Open+Sans:wght@400;600;700&display=swap">
<style>
:root{
  --green:#1f7a45;
  --green-dark:#176036;
  --green-deep:#14502d;
  --grey:#4d4d4d;
  --grey-mid:#8a8a8a;
  --grey-btn:#9a9a9a;
  --line:#d9d9d9;
  --bg:#ffffff;
  --panel:#f2f2f2;
  --map:#2b2b2b;
  --gold:#c9a227;
}
*{box-sizing:border-box;margin:0;padding:0}
html,body{width:1200px;height:3750px;overflow:hidden}
body{font-family:"Open Sans",Arial,sans-serif;color:var(--grey);background:var(--bg);position:relative}
.abs{position:absolute}
.btn{position:absolute;display:flex;align-items:center;justify-content:center;font-weight:600;font-size:15px;color:#fff}
.btn-grey{background:var(--grey-btn)}
.btn-green{background:var(--green)}

/* header */
.site-header{left:0;top:0;width:1200px;height:88px}
.wordmark{font-size:38px;font-weight:600;color:var(--green);letter-spacing:0}
.site-header .wordmark{position:absolute;left:100px;top:18px}
.main-nav{position:absolute;right:100px;top:30px;display:flex;gap:26px;align-items:center;font-size:16px}
.main-nav a{color:var(--grey);text-decoration:none}
.main-nav a.active{color:var(--green)}
.main-nav .login{background:var(--green);color:#fff;padding:6px 14px;font-size:14px}

/* hero */
.hero{left:0;top:88px;width:1200px;height:607px;background:linear-gradient(100deg,#5d6670 0%,#7a838c 40%,#9aa0a6 70%,#c3c6c9 100%)}
.hero-copy{position:absolute;left:100px;top:160px;width:440px;color:#fff}
.hero-copy h1{font-size:30px;font-weight:700;margin-bottom:14px}
.hero-copy p{font-size:19px;font-weight:600;line-height:1.3}
.hero .read{left:100px;top:342px;width:146px;height:36px}
.hero .download{left:265px;top:342px;width:140px;height:36px;border:2px solid #fff;color:#fff;font-weight:400}
.hero-arrows{position:absolute;left:100px;top:397px;display:flex;gap:8px}
.dots{left:580px;top:708px;display:flex;gap:8px}
.dots span{width:8px;height:8px;border-radius:50%;background:#ccc}
.dots span.on{background:var(--green)}

/* welcome */
.welcome{left:100px;top:775px;width:460px}
.welcome h2{font-size:30px;font-weight:400;margin-bottom:18px}
.welcome h3{font-size:21px;font-weight:400;margin-bottom:10px}
.welcome h4{font-size:16px;font-weight:600;margin-bottom:18px}
.welcome p{font-size:14px;line-height:1.45}
.video{left:605px;top:775px;width:495px;height:278px;background:linear-gradient(135deg,#5a5a5a,#8c8c8c 55%,#b5b5b5)}

/* product */
.product-title{left:97px;top:1133px;font-size:32px;font-weight:400}
.product-shot{left:50px;top:1210px;width:475px;height:278px;background:linear-gradient(180deg,#2d2d2d 0%,#3b3b3b 80%,#cfcfcf 100%);border-radius:10px}
.product-copy{left:530px;top:1160px;width:570px;font-size:15px;line-height:1.4}
.product-copy .lead{font-weight:400;margin-bottom:18px}
.product-copy ul{list-style:none}
.product-copy li{position:relative;padding-left:30px;margin-bottom:18px;font-size:14px}
.product-copy li::before{content:"";position:absolute;left:2px;top:7px;width:6px;height:6px;background:var(--grey-mid);border-radius:50%}

/* benefits */
.benefits{left:0;top:1533px;width:1200px;height:435px;background:var(--green);color:#fff;text-align:center}
.benefits h2{position:absolute;top:32px;width:100%;font-size:30px;font-weight:600}
.benefits .sub{position:absolute;top:100px;left:200px;width:800px;font-size:17px;font-weight:600;line-height:1.5}
.benefit-list{position:absolute;top:210px;left:75px;width:1050px;display:flex;justify-content:space-between}
.benefit{width:130px;display:flex;flex-direction:column;align-items:center;gap:12px;font-size:14px;font-weight:600}
.benefits .more{position:absolute;left:518px;top:345px;width:157px;height:33px;border:2px solid #fff;display:flex;align-items:center;justify-content:center;font-size:15px}

/* press */
.press-title{left:0;top:2012px;width:1200px;text-align:center;font-size:30px;font-weight:400}
.press-arrow{top:2018px}
.press-item{top:2092px;width:330px;height:135px}
.press-photo{position:absolute;left:0;top:0;width:125px;height:130px}
.press-body{position:absolute;left:145px;top:0;width:180px}
.press-body h4{font-size:16px;font-weight:600;color:#222;margin-bottom:6px}
.press-body p{font-size:10px;line-height:1.35;margin-bottom:8px}
.press-meta{display:flex;gap:4px;font-size:9px;color:#fff}
.press-meta span{padding:3px 6px;background:var(--grey)}
.press-meta .date{background:var(--green)}

/* clients */
.clients-title{left:0;top:2300px;width:1200px;text-align:center;font-size:30px;font-weight:400}
.client{top:2375px;width:142px;height:83px;border:1px solid var(--line);display:flex;align-items:center;justify-content:center;gap:8px;font-size:14px;font-weight:600;color:var(--grey)}
.client i{width:14px;height:14px;display:block}

/* testimonials */
.testi-title{left:100px;top:2535px;font-size:30px;font-weight:400}
.testi-card{left:113px;top:2603px;width:562px;height:300px;background:var(--green);color:#fff}
.testi-photo{position:absolute;left:25px;top:47px;width:187px;height:193px;background:linear-gradient(160deg,#d8b79a,#b4532c 70%,#7a2e18)}
.testi-text{position:absolute;left:233px;top:40px;width:305px;font-size:12.5px;line-height:1.55}
.testi-text .q{font-size:54px;line-height:0.6;font-weight:700;display:block;margin-bottom:14px}
.testi-tail{left:237px;top:2902px}
.testi-name{left:282px;top:2927px;font-size:16px;font-weight:600;color:#222}
.testi-role{left:282px;top:2950px;font-size:12px;color:var(--grey-mid)}

.book-panel{left:738px;top:2545px;width:362px;height:443px;background:var(--panel)}
.book-panel .wordmark{position:absolute;left:18px;top:18px;font-size:30px}
.book-cover{position:absolute;left:17px;top:85px;width:145px;height:240px;background:linear-gradient(90deg,#222 0 18%,#e4e4e4 18% 100%)}
.book-copy{position:absolute;left:190px;top:110px;width:160px}
.book-copy .soon{font-size:20px;font-weight:700;color:#222;line-height:1.2}
.book-copy .new{font-size:16px;color:var(--green);margin-top:8px}
.book-copy .big{font-size:44px;font-weight:700;color:var(--green);line-height:1}
.book-copy p{font-size:12.5px;margin-top:6px;line-height:1.4}
.book-panel .btn{left:52px;top:360px;width:255px;height:58px;font-size:16px}

/* contact */
.map{left:0;top:3038px;width:1200px;height:462px;background:linear-gradient(135deg,#262626,#333 50%,#2a2a2a)}
.contact-box{left:105px;top:3143px;width:420px;height:145px;background:#fff;text-align:center}
.contact-box h3{font-size:24px;font-weight:400;color:#222;margin-top:10px}
.contact-box p{font-size:12.5px;line-height:1.45;margin-top:6px}
.contact-box .btn{left:0;bottom:0;width:420px;height:34px;font-size:14px}
.pin{left:571px;top:3165px}

/* footer */
.site-footer{left:0;top:3500px;width:1200px;height:195px;background:var(--green);color:#fff}
.foot-col{position:absolute;top:32px;font-size:14px;line-height:1.55}
.foot-col h5{font-size:13px;font-weight:700;margin-bottom:6px}
.foot-col p{width:360px;font-size:13px;line-height:1.4;margin-bottom:16px}
.signup{display:flex}
.signup span{width:300px;height:36px;background:var(--green-deep);padding:8px 14px;font-size:13px}
.signup b{width:46px;height:36px;background:var(--gold);color:#222;display:flex;align-items:center;justify-content:center;font-size:14px}
.bottom-bar{left:0;top:3695px;width:1200px;height:55px;background:var(--green-deep);color:#fff;font-size:12px}
.bottom-bar .copy{position:absolute;left:104px;top:19px}
.bottom-bar .social{position:absolute;right:120px;top:19px;display:flex;gap:14px}
</style>
</head>
<body>

<header class="abs site-header">
  <div class="wordmark">lorentavo</div>
  <nav class="main-nav">
    <a class="active">Home</a><a>About Us</a><a>valuquant®</a><a>Benefits</a><a>Client</a><a>Contact</a><a class="login">Login / Register</a>
  </nav>
</header>

<section class="abs hero" role="img" aria-label="Photo of two business people looking at a tablet">
  <div class="hero-copy">
    <h1>valuquant®</h1>
    <p>valuquant® lets you get a precise overview of how yourbrand operates in the market and a detailed summary of where potential for success can be found - all in real time</p>
  </div>
  <div class="btn btn-green read">Read More</div>
  <div class="btn download">Download Now</div>
  <div class="hero-arrows">
    <svg width="26" height="26" viewBox="0 0 26 26"><circle cx="13" cy="13" r="11" fill="none" stroke="#fff" stroke-width="2"/><path d="M15 8l-5 5 5 5" fill="none" stroke="#fff" stroke-width="2"/></svg>
    <svg width="26" height="26" viewBox="0 0 26 26"><circle cx="13" cy="13" r="11" fill="none" stroke="#fff" stroke-width="2"/><path d="M11 8l5 5-5 5" fill="none" stroke="#fff" stroke-width="2"/></svg>
  </div>
</section>
<div class="abs dots"><span class="on"></span><span></span><span></span></div>

<section class="abs welcome">
  <h2>Welcome To lorentavo</h2>
  <h3>Brand research and brand consulting</h3>
  <h4>lorentavo brings your brand to bear</h4>
  <p>You get an exact brand profile, tailored advertising and thus more successful. You get a precise, fast and reliable onitoring using innovative web methods. They are supported based on current research findings ester.</p>
</section>
<div class="btn btn-grey" style="left:440px;top:1020px;width:130px;height:33px">Know More</div>
<div class="abs video" role="img" aria-label="Video still of a tablet showing a bar chart beside a coffee cup"></div>

<h2 class="abs product-title">valuquant®</h2>
<div class="abs product-shot" role="img" aria-label="Laptop showing the valuquant® dashboard with bar charts"></div>
<section class="abs product-copy">
  <p class="lead">valuquant® lets you get a precise overview of how yourbrand operates in the market and a detailed summary of where potential for success can be found - all in real time</p>
  <ul>
    <li>Lorem ipsum dolor sit amet, consectetur adipiscing elit. Integer dictum, lectus id scelerisque consequat, arcu lacus vehicula nulla.</li>
    <li>eget vehicula nibh odio ut magna. Aliquam eget mi eget magna</li>
    <li>rhoncus sagittis at sed nunc. Nunc in eleifend ligula.</li>
    <li>Proin eget lacus sem. Maecenas nisl metus, rutrum ac velit non, vulputate iaculis eros. Nulla aliquam elementum eros id cursus.</li>
  </ul>
</section>
<div class="btn btn-grey" style="left:970px;top:1450px;width:130px;height:33px">Know More</div>

<section class="abs benefits">
  <h2>Benefits</h2>
  <p class="sub">More successful market development and activities through sound brand analysis and trend modeling using valuquant®»</p>
  <div class="benefit-list">
    <div class="benefit"><svg width="32" height="28" viewBox="0 0 32 28" fill="none" stroke="#fff" stroke-width="2"><rect x="2" y="2" width="28" height="24"/><path d="M6 20l7-8 5 5 9-10"/></svg>Metrics</div>
    <div class="benefit"><svg width="28" height="30" viewBox="0 0 28 30" fill="none" stroke="#fff" stroke-width="2"><path d="M17 2L6 17h8l-3 11 11-15h-8z"/></svg>Trend models</div>
    <div class="benefit"><svg width="36" height="28" viewBox="0 0 36 28" fill="#fff"><circle cx="12" cy="8" r="6"/><circle cx="25" cy="8" r="6"/><path d="M0 28c0-8 6-12 12-12s12 4 12 12zM18 28c0-6 3-10 7-11 6 0 11 4 11 11z"/></svg>Precision</div>
    <div class="benefit"><svg width="26" height="30" viewBox="0 0 26 30" fill="#fff"><path d="M9 2h8l-2 5H11z"/><circle cx="13" cy="19" r="11"/></svg>Cost reduction</div>
    <div class="benefit"><svg width="34" height="28" viewBox="0 0 34 28" fill="none" stroke="#fff" stroke-width="2"><path d="M2 12l8-6 7 4 7-4 8 6-10 10-5-4-5 4z"/></svg>Closeness</div>
    <div class="benefit"><svg width="26" height="30" viewBox="0 0 26 30" fill="#fff"><path d="M13 1l11 4v9c0 8-5 13-11 15C7 27 2 22 2 14V5z"/></svg>Security</div>
    <div class="benefit"><svg width="30" height="28" viewBox="0 0 30 28" fill="none" stroke="#fff" stroke-width="2"><rect x="2" y="12" width="6" height="14"/><path d="M8 13l6-10c3 0 4 2 3 5l-1 4h9c2 0 3 2 2 4l-3 9c-1 1-2 1-3 1H8"/></svg>Fit</div>
    <div class="benefit"><svg width="30" height="28" viewBox="0 0 30 28" fill="none" stroke="#fff" stroke-width="3"><path d="M3 15l8 8L27 4"/></svg>Customer loyalty/ acquisition</div>
  </div>
  <div class="more">Know more</div>
</section>

<h2 class="abs press-title">Press</h2>
<svg class="abs press-arrow" style="left:100px" width="28" height="28" viewBox="0 0 28 28"><circle cx="14" cy="14" r="12" fill="none" stroke="#999" stroke-width="2"/><path d="M16 9l-5 5 5 5" fill="none" stroke="#999" stroke-width="2"/></svg>
<svg class="abs press-arrow" style="left:1078px" width="28" height="28" viewBox="0 0 28 28"><circle cx="14" cy="14" r="12" fill="none" stroke="#999" stroke-width="2"/><path d="M12 9l5 5-5 5" fill="none" stroke="#999" stroke-width="2"/></svg>

<article class="abs press-item" style="left:105px">
  <div class="press-photo" role="img" aria-label="Photo of a businessman in an office" style="background:linear-gradient(160deg,#c9d3dc,#5d6a78)"></div>
  <div class="press-body"><h4>Vivamus lorem lorem</h4><p>mollis varius dolor id, varius metus lesie urna. Cras id tellus nisl. Fusce purus ante, elementum id metus eget, congue pharetra dolor. Sed non mollis quam. Nulla non eros diam.</p><div class="press-meta"><span class="date">05 june 15</span><span>12</span><span>Read More</span></div></div>
</article>
<article class="abs press-item" style="left:445px">
  <div class="press-photo" role="img" aria-label="Photo of a handshake" style="background:linear-gradient(160deg,#7b93ad,#2d4661)"></div>
  <div class="press-body"><h4>Vivamus lorem lorem</h4><p>mollis varius dolor id, varius metus lesie urna. Cras id tellus nisl. Fusce purus ante, elementum id metus eget, congue pharetra dolor. Sed non mollis quam. Nulla non eros diam.</p><div class="press-meta"><span class="date">05 june 15</span><span>07</span><span>Read More</span></div></div>
</article>
<article class="abs press-item" style="left:785px">
  <div class="press-photo" role="img" aria-label="Photo of a team meeting" style="background:linear-gradient(160deg,#e0d8cf,#8a7a6a)"></div>
  <div class="press-body"><h4>Vivamus lorem lorem</h4><p>mollis varius dolor id, varius metus lesie urna. Cras id tellus nisl. Fusce purus ante, elementum id metus eget, congue pharetra dolor. Sed non mollis quam. Nulla non eros diam.</p><div class="press-meta"><span class="date">05 june 15</span><span>07</span><span>Read More</span></div></div>
</article>

<h2 class="abs clients-title">Our Clients</h2>
<svg class="abs" style="left:35px;top:2405px" width="14" height="24" viewBox="0 0 14 24"><path d="M11 2L3 12l8 10" fill="none" stroke="#999" stroke-width="2"/></svg>
<svg class="abs" style="left:1143px;top:2405px" width="14" height="24" viewBox="0 0 14 24"><path d="M3 2l8 10-8 10" fill="none" stroke="#999" stroke-width="2"/></svg>
<div class="abs client" style="left:100px"><i style="background:#e8702a"></i>Logotype</div>
<div class="abs client" style="left:275px"><i style="background:#2a6fb5"></i>YourBusiness</div>
<div class="abs client" style="left:445px"><i style="background:#6b5a3a;border-radius:50%"></i>Logotype</div>
<div class="abs client" style="left:618px"><i style="background:#d9c22a;border-radius:50%"></i>Logotype</div>
<div class="abs client" style="left:790px"><i style="background:#e08a1e;border-radius:50%"></i>Logotype</div>
<div class="abs client" style="left:963px"><i style="background:#3a8fd0"></i>Logotype</div>

<h2 class="abs testi-title">Testimonials</h2>
<section class="abs testi-card">
  <div class="testi-photo" role="img" aria-label="Portrait photo of a smiling client"></div>
  <p class="testi-text"><span class="q">“</span>Lorem Ipsum is simply dummy text of the printing and typesetting industry. Lorem Ipsum has been the industry's standard dummy text ever since the 1500s, when an unknown printer took a galley of type and scrambled it to make a type specimen book. It has survived not only five centuries, but also the leap into electronic typesetting, remaining essentially unchanged.</p>
</section>
<svg class="abs testi-tail" width="40" height="42" viewBox="0 0 40 42"><path d="M0 0h40L0 42z" fill="var(--green)"/></svg>
<div class="abs testi-name">Daniel Fenwick</div>
<div class="abs testi-role">Company Name ,London</div>

<aside class="abs book-panel">
  <div class="wordmark">lorentavo</div>
  <div class="book-cover" role="img" aria-label="The upcoming lorentavo book"></div>
  <div class="book-copy">
    <div class="soon">Coming<br>Soon.....</div>
    <div class="new">OUR NEW</div>
    <div class="big">BOOK</div>
    <p>Lorem Ipsum is simply dummy text of the printing and typesetting industry.</p>
  </div>
  <div class="btn btn-green">REGISTER NOW !</div>
</aside>

<section class="abs map" role="img" aria-label="Dark street map of the office area"></section>
<svg class="abs pin" width="24" height="34" viewBox="0 0 24 34"><path d="M12 1C6 1 1 6 1 12c0 8 11 21 11 21s11-13 11-21C23 6 18 1 12 1z" fill="#e23b3b"/><circle cx="12" cy="12" r="4" fill="#fff"/></svg>
<section class="abs contact-box">
  <h3>Contact Us</h3>
  <p>lorentavo ltd. Lindenweg 14, CH-8000 Musterdorf,<br>Cell: +41 00 000 00 00 ,Tel.: +41 00 000 00 01<br>info@lorentavo.ch</p>
  <div class="btn btn-green">SEND US AN EMAIL</div>
</section>

<footer class="abs site-footer">
  <div class="foot-col" style="left:110px"><h5>VALUE</h5>About<br>FAQ<br>Blog<br>Service<br>Customer</div>
  <div class="foot-col" style="left:248px"><h5>AFFILIATE</h5>Orbitel<br>Kaizo Works<br>Aerodyne<br>Vistacast</div>
  <div class="foot-col" style="left:398px"><h5>AFFILIATE</h5>Orbitel<br>Kaizo Works<br>Aerodyne<br>Vistacast</div>
  <div class="foot-col" style="left:580px"><h5>VALUE</h5>About<br>FAQ<br>Blog<br>Service<br>Customer</div>
  <div class="foot-col" style="left:750px"><h5>GET SERVED</h5><p>Maecenas tincidunt bibendum nisl, ac ultrices quam laoreet adipiscing</p><div class="signup"><span>yourname@email.com</span><b>GO</b></div></div>
</footer>
<div class="abs bottom-bar">
  <span class="copy">Yourwebsite.com © Copyright 2014, all rights reserved.</span>
  <span class="social"><span>chatterbay</span><span>quipline</span></span>
</div>

</body>
</html>
```